New banner graphics for Tondix.com website

I've developed a software tool that helps businesses ensure they are working on their most valuable and important work.

I would like a banner graphic for my home page (www.tondix.com) that can somehow capture the value of focus and intentional outcomes.

I had an initial thought of a starry sky that shifts focus to a few bright stars, but while that might sound ok, I think my idea is lame hence I'm coming to you guys.

My sites two primary colors are a soft purple and gray.
#919EC1(purple)
#9E9E9E (gray)

Target Market(s)

B2B for enterprises. Typical customers are CFOs, CIOs/Heads of IT

Industry/Entity Type

Business Software

Number of Pages Required

1 page

Font styles to use
Sans Serif

Colors
b8a6cd
cedeed

Requirements
Must have
• I use Divi as my Wordpress theme and the current main landing page can be seen at www.tondix.com.
• My logo colors are:
• #919EC1(purple)
• #9E9E9E (gray)
Should not have
• Lots of distraction or visual "noise". I want to re-enforce the message that my software is focused on their business and not my products or website.

```html
<!DOCTYPE html>
<html lang="en">
<head>
<meta charset="utf-8">
<title>Is Your Business Strategy</title>
<link rel="stylesheet" href="https://fonts.googleapis.com/css2?family=Roboto+Slab:wght@700&family=Raleway:ital,wght@0,500;0,700;1,400&display=swap">
<style>
  :root {
    --bg-light: #e6e6e8;
    --bg-mid: #b9b9bd;
    --bg-dark: #8d8f95;
    --wood: #d9c3a0;
    --band: rgba(70, 70, 74, 0.55);
    --text: #ffffff;
    --text-soft: rgba(255, 255, 255, 0.92);
  }
  * { margin: 0; padding: 0; box-sizing: border-box; }
  html, body { width: 1200px; height: 675px; overflow: hidden; }
  body { background: var(--bg-mid); }
  .banner {
    position: relative;
    width: 1200px;
    height: 675px;
    overflow: hidden;
  }
  .hero-photo {
    position: absolute;
    inset: 0;
    background:
      radial-gradient(ellipse 120px 300px at 630px 470px, var(--wood) 0%, rgba(217,195,160,0.55) 55%, transparent 100%),
      radial-gradient(ellipse 260px 200px at 330px 220px, #d8c8bc 0%, rgba(216,200,188,0) 100%),
      radial-gradient(ellipse 220px 420px at 1080px 350px, #7d8088 0%, rgba(125,128,136,0) 100%),
      linear-gradient(100deg, var(--bg-light) 0%, var(--bg-mid) 45%, var(--bg-dark) 100%);
  }
  .band {
    position: absolute;
    left: 0;
    top: 195px;
    width: 1200px;
    height: 351px;
    background: var(--band);
  }
  .title-frame {
    position: absolute;
    left: 290px;
    top: 225px;
    width: 610px;
    height: 64px;
    border: 2px solid var(--text-soft);
    display: flex;
    align-items: center;
    justify-content: center;
  }
  .title {
    font-family: "Roboto Slab", serif;
    font-weight: 700;
    font-size: 39px;
    color: var(--text);
    letter-spacing: 0.3px;
    text-shadow: 0 2px 4px rgba(0,0,0,0.35);
    white-space: nowrap;
  }
  .contrast-list {
    position: absolute;
    left: 0;
    top: 345px;
    width: 1200px;
    list-style: none;
    font-family: "Raleway", sans-serif;
    font-size: 23px;
    color: var(--text);
    text-shadow: 0 1px 3px rgba(0,0,0,0.3);
  }
  .contrast-row {
    position: relative;
    height: 40px;
    line-height: 40px;
    white-space: nowrap;
  }
  .contrast-good {
    position: absolute;
    right: 754px;
    font-weight: 500;
    text-transform: uppercase;
  }
  .contrast-or {
    position: absolute;
    left: 481px;
    font-weight: 700;
  }
  .contrast-bad {
    position: absolute;
    left: 548px;
    font-style: italic;
    font-weight: 400;
    text-transform: uppercase;
    color: var(--text-soft);
  }
</style>
</head>
<body>
  <main class="banner">
    <div class="hero-photo" role="img" aria-label="Blurred photo of a businessman in a suit carefully pulling a wooden block from a stacked block tower"></div>
    <div class="band"></div>
    <div class="title-frame">
      <h1 class="title">Is Your Business Strategy</h1>
    </div>
    <ul class="contrast-list">
      <li class="contrast-row"><span class="contrast-good">Written down</span><span class="contrast-or">OR</span><span class="contrast-bad">Loose thoughts – on the&nbsp; best of days</span></li>
      <li class="contrast-row"><span class="contrast-good">Driving projects</span><span class="contrast-or">OR</span><span class="contrast-bad">Just a set of slides tacked to walls</span></li>
      <li class="contrast-row"><span class="contrast-good">Shared with the team</span><span class="contrast-or">OR</span><span class="contrast-bad">Kept top secret just to be safe</span></li>
      <li class="contrast-row"><span class="contrast-good">Measurable</span><span class="contrast-or">OR</span><span class="contrast-bad">More art than science</span></li>
    </ul>
  </main>
</body>
</html>
```